Interior Design/ decoration business card design

This card is for my Interior Design and Decoration business and later I will also be selling homewares. I would like the card to be very simple in design and like either white, duck egg blue , aquas or metallics on a flat mat card excellent quality card. It needs to be well designed as that is my field. I dont like fuss, the simpler the better. I would like a styalised brim under the name brim if possible. SIMPLE, STYLISH, CLASSIC, TASTEFUL

Target Market(s)

40 + year olds who are building or rennovating.

Industry/Entity Type

Business

Contact Information for Business Card

Brim
styling, design, homeware

Marnie Callow
p 0427163958
e marnie@brimhouse.com.au
w brimhouse.com.au

Requirements
Must have
• very simple, stylish, classic, sophisticated. Simple and easy to read text that is a print similar to attached image. I like simple round A's though not as in attached image.

Double sided. It wont save as double sided for some reason!!
Should not have
• not too much colour, No animated / cartoon pictures.

```html
<!DOCTYPE html>
<html lang="en">
<head>
<meta charset="utf-8">
<title>Brim – Business Card</title>
<link rel="stylesheet" href="https://fonts.googleapis.com/css2?family=Arimo:wght@400;700&display=swap">
<style>
  :root {
    --backdrop: #a3a3a3;
    --card-front: #ffffff;
    --card-back: #bdd9d6;
    --ink: #1e1e1e;
    --ink-soft: #333333;
    --accent: #d42a2a;
    --card-shadow: rgba(0, 0, 0, 0.28);
  }
  * { box-sizing: border-box; margin: 0; padding: 0; }
  html, body {
    width: 1200px;
    height: 960px;
    overflow: hidden;
    background: var(--backdrop);
    font-family: "Arimo", Arial, sans-serif;
    color: var(--ink);
  }
  .canvas {
    position: relative;
    width: 1200px;
    height: 960px;
  }
  .card {
    position: absolute;
    width: 640px;
    height: 380px;
    border-radius: 22px;
    box-shadow: 0 6px 18px var(--card-shadow);
  }
  .card--front {
    left: 110px;
    top: 80px;
    background: var(--card-front);
  }
  .card--back {
    left: 450px;
    top: 500px;
    background: var(--card-back);
  }
  .brand-name {
    position: absolute;
    font-weight: 400;
    letter-spacing: 0.28em;
    color: var(--ink-soft);
    line-height: 1;
  }
  .card--front .brand-name {
    left: 0;
    right: 0;
    top: 120px;
    text-align: center;
    font-size: 76px;
    padding-left: 0.28em;
  }
  .tagline {
    position: absolute;
    left: 0;
    right: 0;
    bottom: 70px;
    display: flex;
    justify-content: center;
    align-items: center;
    gap: 18px;
    font-size: 18px;
    color: var(--ink);
  }
  .tagline__divider {
    width: 2px;
    height: 26px;
    background: var(--accent);
  }
  .card--back .brand-name {
    right: 70px;
    top: 110px;
    font-size: 56px;
  }
  .holder-name {
    position: absolute;
    left: 50px;
    top: 150px;
    font-size: 22px;
    font-weight: 700;
    font-variant: small-caps;
    letter-spacing: 0.02em;
    color: var(--ink);
  }
  .holder-name__surname { color: var(--accent); }
  .contact-list {
    position: absolute;
    left: 50px;
    top: 240px;
    list-style: none;
    font-size: 18px;
    color: var(--ink);
  }
  .contact-list__item {
    display: flex;
    align-items: center;
    gap: 10px;
    height: 27px;
  }
  .contact-list__icon {
    width: 20px;
    height: 18px;
    flex: none;
  }
</style>
</head>
<body>
  <main class="canvas">
    <section class="card card--front" aria-label="Card front">
      <h1 class="brand-name">brim</h1>
      <p class="tagline">
        <span>Decoration</span>
        <span class="tagline__divider"></span>
        <span>styling</span>
        <span class="tagline__divider"></span>
        <span>Homeware</span>
      </p>
    </section>

    <section class="card card--back" aria-label="Card back">
      <p class="holder-name">Marnie <span class="holder-name__surname">Callow</span></p>
      <ul class="contact-list">
        <li class="contact-list__item">
          <svg class="contact-list__icon" viewBox="0 0 20 18" aria-hidden="true">
            <path d="M1 6 Q10 0 19 6 L17 8 L14 6.5 L14 5 Q10 3.5 6 5 L6 6.5 L3 8 Z" fill="#1e1e1e"/>
            <rect x="3" y="9" width="14" height="8" rx="1.5" fill="#1e1e1e"/>
            <circle cx="10" cy="13" r="2" fill="#bdd9d6"/>
          </svg>
          <span>0427163958</span>
        </li>
        <li class="contact-list__item">
          <svg class="contact-list__icon" viewBox="0 0 20 18" aria-hidden="true">
            <rect x="1" y="3" width="18" height="12" fill="#1e1e1e"/>
            <path d="M1.5 3.5 L10 10 L18.5 3.5" fill="none" stroke="#bdd9d6" stroke-width="1.4"/>
          </svg>
          <span>marnie@brimhouse.com.au</span>
        </li>
        <li class="contact-list__item">
          <svg class="contact-list__icon" viewBox="0 0 20 18" aria-hidden="true">
            <g fill="none" stroke="#1e1e1e" stroke-width="1.2">
              <circle cx="10" cy="9" r="8"/>
              <ellipse cx="10" cy="9" rx="3.5" ry="8"/>
              <line x1="2" y1="9" x2="18" y2="9"/>
              <line x1="3.5" y1="5" x2="16.5" y2="5"/>
              <line x1="3.5" y1="13" x2="16.5" y2="13"/>
            </g>
          </svg>
          <span>brimhouse.com.au</span>
        </li>
      </ul>
      <p class="brand-name">brim</p>
    </section>
  </main>
</body>
</html>
```